Business Card for a Life Coaching Company

MOSSVALE is a Life Coaching company that was initiated to support people who want to transform thier life or ana aspect of it.
our slogan is : "Dream. Believe. Succeed"
our logo is uploaded.
The name of the company implies that leadership, strength and wisdom required to change your life.
We want an attractive business card that would give an impression of reliability, support and change. so we really want it unique. Here are some examples of unique cards:

http://www.pixelharbornotes.example/2009/05/100-really-creative-business-cards/

MossVale is a life coaching organization focusing on individual transformation through the application of relevant and timeless principles of success.  MossVale believes that real, sustainable life transformations are brought about by tuning into the timeless wisdom we each carry in our hearts while boldy acting in the direction of our dreams.

Contacts on the card:
Address: 7 Tarek Ibn Nabil Heliopolis Cairo Egypt
Tel: +202 24 81 37 52
Fax: +202 24 81 37 19
Mobile: +2 012 574 9026 (Nadia Sherif)
+2 0199915815 (Kamal Rashidi)

By the way, our temporary website is http://www.mossvale.example

We have attached an .eps file with various configurations of our logo.

```html
<!DOCTYPE html>
<html lang="en">
<head>
<meta charset="utf-8">
<title>MossVale – Business Card</title>
<link href="https://fonts.googleapis.com/css2?family=Crimson+Text:wght@400&display=swap" rel="stylesheet">
<style>
  :root {
    --backdrop: #e6e5e6;
    --card: #ffffff;
    --brand-orange: #ff6600;
    --brand-grey: #8f8f8f;
    --shadow: rgba(0, 0, 0, 0.5);
  }
  * { margin: 0; padding: 0; box-sizing: border-box; }
  html, body {
    width: 1050px;
    height: 1200px;
    overflow: hidden;
    background: var(--backdrop);
    font-family: "Crimson Text", Georgia, serif;
  }
  .canvas { position: relative; width: 1050px; height: 1200px; }
  .card {
    position: absolute;
    left: 190px;
    width: 680px;
    height: 390px;
    background: var(--card);
    box-shadow: 0 12px 12px -2px var(--shadow);
    overflow: hidden;
  }
  .card--front { top: 165px; }
  .card--back { top: 620px; }

  /* Front */
  .brand {
    position: absolute;
    left: 36px;
    top: 132px;
    display: flex;
    align-items: center;
    gap: 14px;
  }
  .brand__mark {
    width: 48px;
    height: 48px;
    background: var(--brand-orange);
  }
  .brand__name {
    color: var(--brand-grey);
    font-size: 54px;
    line-height: 50px;
    letter-spacing: 1px;
    text-transform: uppercase;
  }
  .tagline {
    position: absolute;
    left: 286px;
    top: 161px;
    width: 400px;
    height: 50px;
    border: 2px solid var(--brand-orange);
    border-right: none;
    color: var(--brand-orange);
    font-size: 23px;
    line-height: 46px;
    padding-left: 12px;
  }

  /* Back */
  .contact {
    position: absolute;
    left: 0;
    top: 82px;
    width: 404px;
    text-align: center;
    color: var(--brand-orange);
    font-size: 18px;
  }
  .contact__address { line-height: 24px; }
  .contact__people { margin-top: 32px; line-height: 32px; }
  .contact__lines { margin-top: 22px; line-height: 28px; }
  .contact__web { margin-top: 18px; line-height: 24px; }
  .card__art {
    position: absolute;
    left: 395px;
    top: 0;
    width: 285px;
    height: 390px;
    background: linear-gradient(160deg, #ff6600 0%, #ff8a3d 55%, #ff6600 100%);
  }
</style>
</head>
<body>
<main class="canvas">
  <section class="card card--front">
    <div class="brand">
      <span class="brand__mark"></span>
      <span class="brand__name">Moss<br>Vale</span>
    </div>
    <p class="tagline">"Dream. Believe. Succeed"</p>
  </section>

  <section class="card card--back">
    <div class="contact">
      <p class="contact__address">7 Tarek Ibn Nabil Heliopolis Cairo Egypt</p>
      <p class="contact__people">(Nadia Sherif)+2 012 574 9026<br>(Kamal Rashidi)+2 0196632470</p>
      <p class="contact__lines">Tel: +202 24 81 37 52<br>Fax: +202 24 81 37 19</p>
      <p class="contact__web">www.mossvale.example</p>
    </div>
    <div class="card__art" role="img" aria-label="Large orange brush-stroke mane illustration bleeding off the card edge"></div>
  </section>
</main>
</body>
</html>
```